Specialised investor in e-mobility and energy wants business card design

We need a business card design that fits our existing corporate design. <The look and feel must be 'sharp'/'clean', dynamic, communicate momentum, professionalism etc (as one would imagine from a firm in the financial sector). We like the idea of a reverse-side of the card that includes the logo, and the name and contact details on the other. We expect the deliverable to be whatever format might be required to be able to get cards printed directly by a service such as kelmo press. Our website is www.zub.capital

```html
<!DOCTYPE html>
<html lang="en">
<head>
<meta charset="utf-8">
<title>Zub Capital business card</title>
<link href="https://fonts.googleapis.com/css2?family=Montserrat:wght@400;500;700&display=swap" rel="stylesheet">
<style>
:root{
  --backdrop:#e3e3e0;
  --paper:#ffffff;
  --green-dark:#2f4f22;
  --green-light:#86b24a;
  --ink:#333333;
}
*{margin:0;padding:0;box-sizing:border-box}
html,body{width:1200px;height:801px;overflow:hidden}
body{background:var(--backdrop);font-family:'Montserrat',sans-serif;position:relative}
.card{position:absolute;top:250px;width:520px;height:300px;background:var(--paper);
  box-shadow:0 6px 18px rgba(0,0,0,.12);overflow:hidden}
.card--front{left:50px}
.card--back{left:630px;border-bottom:4px solid var(--green-light)}
.wordmark{position:absolute;display:flex;align-items:center;gap:10px;color:var(--green-dark);font-weight:500;letter-spacing:.5px;white-space:nowrap}
.wordmark__dot{border-radius:50%;background:var(--green-light)}
.card--front .wordmark{left:30px;top:128px;font-size:30px}
.card--front .wordmark__dot{width:12px;height:12px}
.card--back .wordmark{left:50%;top:50%;transform:translate(-50%,-50%);font-size:58px}
.card--back .wordmark__dot{width:22px;height:22px}
.divider{position:absolute;left:232px;top:44px;width:1.5px;height:190px;background:var(--green-light)}
.details{position:absolute;left:256px;top:40px;color:var(--ink)}
.details__name{font-size:20px;font-weight:700;color:var(--green-light);letter-spacing:.5px}
.details__role{font-size:14px;margin-top:2px}
.contacts{list-style:none;margin-top:18px;font-size:13.5px;line-height:20px}
.contacts li{display:flex;align-items:center;gap:8px}
.contacts svg{width:12px;height:12px;fill:var(--green-light)}
.details__company{margin-top:16px;font-size:13.5px;color:var(--green-light)}
.details__city{font-size:13.5px}
.band{position:absolute;left:0;bottom:0;width:520px;height:26px}
</style>
</head>
<body>
<section class="card card--front">
  <div class="wordmark"><span class="wordmark__dot"></span>zub capital</div>
  <div class="divider"></div>
  <div class="details">
    <div class="details__name">MARCUS HALLBERG</div>
    <div class="details__role">Managing Director</div>
    <ul class="contacts">
      <li><svg viewBox="0 0 12 12"><path d="M2 1h3l1 3-2 1a7 7 0 0 0 3 3l1-2 3 1v3a1 1 0 0 1-1 1A10 10 0 0 1 1 2a1 1 0 0 1 1-1z"/></svg>+41 79 555 0148</li>
      <li><svg viewBox="0 0 12 12"><path d="M0 2h12v8H0z M0 2l6 5 6-5" stroke="#fff" stroke-width="1"/></svg>marcus@zub.capital</li>
      <li><svg viewBox="0 0 12 12"><circle cx="6" cy="6" r="6"/><path d="M0 6h12M6 0v12" stroke="#fff" stroke-width="1"/></svg>www.zub.capital</li>
    </ul>
    <div class="details__company">Zub Capital S.A.</div>
    <div class="details__city">Geneva, Switzerland</div>
  </div>
  <svg class="band" viewBox="0 0 520 26" aria-hidden="true">
    <polygon points="0,0 250,0 236,26 0,26" fill="var(--green-dark)"/>
    <polygon points="260,12 520,12 520,26 254,26" fill="var(--green-light)"/>
  </svg>
</section>
<section class="card card--back">
  <div class="wordmark"><span class="wordmark__dot"></span>zub capital</div>
</section>
</body>
</html>
```